Business Card Design

New business card design

Target Market(s)

Residential & Commercial Property Managers

Industry/Entity Type

Plumbing Services

Contact Information for Business Card

Name - Rowan Keddle, title - Director, Phone Number - 0431 286 517, email - rowan@tbk-plumbing.com.au, Company ABN - 73 215 904 386,

Font styles to use
Sans Serif

Colors
0054AA
0677BA
7BADD7
CADEEF
E8F1F8

```html
<!DOCTYPE html>
<html lang="en">
<head>
<meta charset="utf-8">
<title>TBK Plumbing Services – Business Card</title>
<link rel="stylesheet" href="https://fonts.googleapis.com/css2?family=Michroma&family=Roboto:wght@300;400&display=swap">
<style>
  :root {
    --stage: #2b2b2d;
    --card-white: #ffffff;
    --card-black: #141416;
    --ink: #1d2228;
    --ink-soft: #3a3f45;
    --tagline: #7a6e66;
    --accent: #1aa3e0;
    --rule: #1d2228;
    --logo-light: #ffffff;
  }
  * { box-sizing: border-box; margin: 0; padding: 0; }
  html, body {
    width: 1200px; height: 1108px; overflow: hidden;
    background: var(--stage);
  }
  .stage {
    position: relative; width: 1200px; height: 1108px;
    display: flex; justify-content: center; align-items: center; gap: 80px;
  }
  .card {
    position: relative; width: 400px; height: 654px;
    border-radius: 26px; overflow: hidden;
    box-shadow: 0 18px 40px rgba(0,0,0,.45);
  }
  .card--front {
    background: var(--card-white);
    display: flex; flex-direction: column; align-items: center;
    font-family: "Roboto", sans-serif; color: var(--ink);
  }
  .brand {
    font-family: "Roboto", sans-serif; font-weight: 300;
    text-align: center; line-height: 1;
  }
  .brand__name { display: block; font-size: 108px; letter-spacing: 2px; }
  .brand__tagline { display: block; font-size: 13px; letter-spacing: 9px; margin-top: 14px; }
  .card--front .brand { color: var(--ink); margin-top: 110px; }
  .brand__dot {
    display: inline-block; width: 14px; height: 14px; border-radius: 50%;
    background: var(--accent); margin-top: 12px;
  }
  .contact { margin-top: 120px; text-align: center; }
  .contact__name {
    font-family: "Michroma", sans-serif; font-size: 25px; letter-spacing: 1px;
    color: var(--ink);
  }
  .contact__title { font-size: 21px; color: var(--accent); margin-top: 6px; }
  .rule { width: 34px; height: 2px; background: var(--rule); margin: 14px auto; }
  .contact__line { font-size: 20px; color: var(--ink-soft); line-height: 1.45; }
  .contact__abn { font-size: 20px; color: var(--ink-soft); }
  .contact__abn-label { color: var(--accent); }

  .card--back { background: var(--card-black); }
  .drop-texture {
    position: absolute; inset: 0;
    background: linear-gradient(150deg, #2c2c30 0%, #1a1a1d 45%, #0c0c0e 100%);
  }
  .card--back .brand {
    position: absolute; left: 0; right: 0; bottom: 120px;
    color: var(--logo-light);
  }
</style>
</head>
<body>
  <main class="stage">
    <section class="card card--front" aria-label="Business card front">
      <div class="brand">
        <span class="brand__name">tbk</span>
        <span class="brand__tagline">plumbing services</span>
        <span class="brand__dot" aria-hidden="true"></span>
      </div>
      <div class="contact">
        <p class="contact__name">ROWAN KEDDLE</p>
        <p class="contact__title">Director</p>
        <div class="rule"></div>
        <p class="contact__line">0431 286 517</p>
        <p class="contact__line">rowan@tbk-plumbing.com.au</p>
        <div class="rule"></div>
        <p class="contact__abn"><span class="contact__abn-label">Company ABN</span> - 73 215 904 386</p>
      </div>
    </section>

    <section class="card card--back" aria-label="Business card back">
      <div class="drop-texture" role="img" aria-label="Glossy black pattern of repeating water droplets"></div>
      <div class="brand">
        <span class="brand__name">tbk</span>
        <span class="brand__tagline">plumbing services</span>
      </div>
    </section>
  </main>
</body>
</html>
```